Corvex Hiring Partners Business Cards

Business cards with logo design for a new recruiting company called "Corvex Hiring Partners"

incorporate RED & BLUE colors

Final design should reflect strength - clean, elegant design

Company name superimposed upon graphic (Greek Columns)

Please see attached Photos!!!

Industry/Entity Type

Business

Font styles to use
Decorative

Colors
ec2027
0555a3
85cae6

Requirements
Must have
• Must look very similar to attached design!!!

Want Company name superimposed upon graphic (Greek Columns)

Tag line at bottom must be included:
"Building Stronger Companies Through Remarkable Teams"

```html
<!DOCTYPE html>
<html lang="en">
<head>
<meta charset="UTF-8">
<title>Corvex Hiring Partners – Business Card</title>
<link rel="stylesheet" href="https://fonts.googleapis.com/css2?family=EB+Garamond:wght@400;500&display=swap">
<style>
  :root {
    --brand-red: #ec2027;
    --brand-blue: #0555a3;
    --brand-sky: #85cae6;
    --card-white: #ffffff;
    --ink: #222222;
    --divider: #f2c9cb;
    --backdrop: #5b3d27;
  }
  html, body {
    margin: 0;
    padding: 0;
    width: 1200px;
    height: 845px;
    overflow: hidden;
    background: var(--backdrop);
    font-family: "EB Garamond", Georgia, serif;
  }
  .canvas {
    position: relative;
    width: 1200px;
    height: 845px;
  }
  .business-card {
    position: absolute;
    left: 80px;
    top: 125px;
    width: 1040px;
    height: 594px;
    background: var(--card-white);
    box-shadow: 0 6px 24px rgba(0,0,0,0.35);
  }
  .brand-block {
    position: absolute;
    left: 90px;
    top: 120px;
    width: 360px;
    display: flex;
    align-items: center;
    gap: 26px;
  }
  .brand-mark {
    flex: 0 0 auto;
    width: 62px;
    height: 62px;
    border-radius: 50%;
    background: var(--brand-sky);
  }
  .brand-name {
    margin: 0;
    font-size: 46px;
    font-weight: 500;
    line-height: 1.05;
    color: var(--brand-blue);
    letter-spacing: 1px;
  }
  .card-divider {
    position: absolute;
    left: 505px;
    top: 100px;
    width: 2px;
    height: 250px;
    background: linear-gradient(to bottom, transparent, var(--divider) 15%, var(--divider) 85%, transparent);
  }
  .contact-block {
    position: absolute;
    left: 555px;
    top: 108px;
  }
  .person-name {
    margin: 0 0 42px;
    font-size: 40px;
    font-weight: 400;
    color: var(--brand-blue);
  }
  .contact-list {
    list-style: none;
    margin: 0;
    padding: 0;
  }
  .contact-item {
    display: flex;
    align-items: center;
    gap: 14px;
    font-size: 23px;
    color: var(--ink);
    margin-bottom: 14px;
  }
  .contact-icon {
    width: 22px;
    height: 22px;
    fill: var(--ink);
  }
  .tagline {
    position: absolute;
    left: 0;
    right: 0;
    bottom: 92px;
    margin: 0;
    padding-left: 120px;
    text-align: center;
    font-size: 33px;
    color: var(--brand-red);
  }
</style>
</head>
<body>
<div class="canvas">
  <article class="business-card">
    <div class="brand-block">
      <span class="brand-mark" aria-hidden="true"></span>
      <h1 class="brand-name">Corvex<br>Hiring<br>Partners</h1>
    </div>

    <div class="card-divider" aria-hidden="true"></div>

    <div class="contact-block">
      <h2 class="person-name">Daniel R. Whitcomb</h2>
      <ul class="contact-list">
        <li class="contact-item">
          <svg class="contact-icon" viewBox="0 0 24 24" aria-hidden="true"><circle cx="12" cy="12" r="11" fill="none" stroke="#222" stroke-width="2"/><path d="M8 6c1 0 2 2 2 3s-1 1-1 2 2 4 3 4 1-1 2-1 3 1 3 2-1 3-3 3c-4 0-9-5-9-9 0-2 2-4 3-4z"/></svg>
          512-555-0142
        </li>
        <li class="contact-item">
          <svg class="contact-icon" viewBox="0 0 24 24" aria-hidden="true"><path d="M2 9l10-6 10 6v12H2z"/><path d="M3 10l9 6 9-6" fill="none" stroke="#fff" stroke-width="1.6"/></svg>
          DWhitcomb@CorvexHP.com
        </li>
        <li class="contact-item">
          <svg class="contact-icon" viewBox="0 0 24 24" aria-hidden="true"><g fill="none" stroke="#222" stroke-width="2"><circle cx="12" cy="12" r="10"/><ellipse cx="12" cy="12" rx="4.5" ry="10"/><path d="M2 12h20M4 7h16M4 17h16"/></g></svg>
          www.CorvexHP.com
        </li>
      </ul>
    </div>

    <p class="tagline">Building Stronger Companies Through Remarkable Teams</p>
  </article>
</div>
</body>
</html>
```